Simple and Clean business card design

We would like the design to be simple clean and to incorporate our colors.

We are open to your design and talent, we have the dots in our logo as we think of it as data points and we connect data points for people.

We are open to see the great creative and clean design you bring to the table

Contact Information for Business Card

please include: name, position, email, phone and website

Font styles to use
Sans Serif

Requirements
Must have
• my colors incorporated, simplicity
Nice to have
• lots of white space, simplicity
Should not have
• complexicity/ complex art

```html
<!DOCTYPE html>
<html lang="en">
<head>
<meta charset="utf-8">
<title>Nectra Business Card</title>
<link href="https://fonts.googleapis.com/css2?family=Arimo:wght@400;700&family=Oswald:wght@600&display=swap" rel="stylesheet">
<style>
  :root {
    --backdrop: #0b0b0b;
    --card: #161616;
    --ink: #ffffff;
    --accent-blue: #3f7ff2;
    --rule: #5a5a5a;
  }
  * { margin: 0; padding: 0; box-sizing: border-box; }
  html, body {
    width: 1200px;
    height: 900px;
    overflow: hidden;
    background: var(--backdrop);
  }
  .canvas {
    position: relative;
    width: 1200px;
    height: 900px;
    display: flex;
    flex-direction: column;
    align-items: center;
    justify-content: center;
    gap: 48px;
  }
  .card {
    width: 640px;
    height: 366px;
    background: var(--card);
    box-shadow: 0 10px 30px rgba(0,0,0,0.6);
    position: relative;
  }
  .card-front {
    display: flex;
    align-items: center;
    justify-content: center;
    gap: 16px;
  }
  .brand-dot {
    width: 26px;
    height: 26px;
    border-radius: 50%;
    background: var(--accent-blue);
  }
  .brand-name {
    font-family: "Arimo", Arial, sans-serif;
    font-weight: 700;
    font-size: 92px;
    letter-spacing: 1px;
    color: var(--ink);
    line-height: 1;
  }
  .card-back {
    display: flex;
    align-items: center;
    justify-content: center;
    padding-top: 40px;
  }
  .identity {
    text-align: right;
    padding-right: 28px;
  }
  .person-name {
    font-family: "Oswald", "Arial Narrow", sans-serif;
    font-weight: 600;
    font-size: 34px;
    color: var(--accent-blue);
    line-height: 1;
    letter-spacing: 0.5px;
  }
  .person-role {
    font-family: "Arimo", Arial, sans-serif;
    font-size: 17px;
    color: var(--ink);
    margin-top: 6px;
  }
  .divider {
    width: 1px;
    height: 92px;
    background: var(--rule);
  }
  .contact-list {
    list-style: none;
    padding-left: 22px;
    display: flex;
    flex-direction: column;
    gap: 6px;
  }
  .contact-item {
    display: flex;
    align-items: center;
    gap: 8px;
    font-family: "Arimo", Arial, sans-serif;
    font-size: 17px;
    color: var(--ink);
  }
  .contact-icon { width: 22px; height: 22px; flex: none; }
</style>
</head>
<body>
  <main class="canvas">
    <section class="card card-front">
      <span class="brand-dot"></span>
      <span class="brand-name">Nectra</span>
    </section>

    <section class="card card-back">
      <div class="identity">
        <h1 class="person-name">DANA WHITLOW</h1>
        <p class="person-role">Founder/ CEO</p>
      </div>
      <div class="divider"></div>
      <ul class="contact-list">
        <li class="contact-item">
          <svg class="contact-icon" viewBox="0 0 24 24" aria-hidden="true">
            <circle cx="12" cy="12" r="10.5" fill="none" stroke="var(--accent-blue)" stroke-width="2"/>
            <path d="M8.5 7.5c.6-.6 1.3-.6 1.7 0l1 1.5c.3.5.2 1-.2 1.4l-.6.5c.5 1.2 1.4 2.1 2.6 2.6l.5-.6c.4-.4.9-.5 1.4-.2l1.5 1c.6.4.6 1.1 0 1.7-1.2 1.2-3 1-5-.6-2.1-1.7-3.6-4.1-2.9-7.3z" fill="var(--accent-blue)"/>
          </svg>
          <span>555-014-2286</span>
        </li>
        <li class="contact-item">
          <svg class="contact-icon" viewBox="0 0 24 24" aria-hidden="true">
            <circle cx="12" cy="12" r="10.5" fill="none" stroke="var(--accent-blue)" stroke-width="2"/>
            <rect x="6.5" y="8.5" width="11" height="7.5" fill="var(--accent-blue)"/>
            <path d="M6.5 8.5l5.5 4 5.5-4" fill="none" stroke="var(--card)" stroke-width="1.2"/>
          </svg>
          <span>dana.whitlow@nectra.one</span>
        </li>
        <li class="contact-item">
          <svg class="contact-icon" viewBox="0 0 24 24" aria-hidden="true">
            <circle cx="12" cy="12" r="10.5" fill="none" stroke="var(--accent-blue)" stroke-width="2"/>
            <circle cx="12" cy="12" r="6" fill="none" stroke="var(--accent-blue)" stroke-width="1.3"/>
            <ellipse cx="12" cy="12" rx="2.6" ry="6" fill="none" stroke="var(--accent-blue)" stroke-width="1.1"/>
            <path d="M6 12h12M7 9h10M7 15h10" stroke="var(--accent-blue)" stroke-width="1.1"/>
          </svg>
          <span>www.Nectra.one</span>
        </li>
      </ul>
    </section>
  </main>
</body>
</html>
```